MODERN & SLEEK CATALOGUE FOR FOOD AND BEVERAGES

VELMORIS & TRADE needs a new catalogue to present its offers to international distributors and retailers.
Our Product list includes; Wine, Olive oil, Spanish ham, Cheese etc....
Our target audience is mainly located in Japan, South Korea, Hong Kong Singapore, Malaysia, Panama, and the US.
Please, bear in mind we will use THE catalogue with our tablets during presentation meetings. Thanks so much.
Updates
Dear Designers,
We have requested the HD images and Pictures of each product to the vendors, so we can include them to the catalogue.
We would love to have 2 icons/vectors for the "tasting notes" and the "awards" in our Wine categories.
Any suggestions or requests are most welcome from you.
Many thanks. Kind regards,
Reason: As we only have two designs we would like to extend our project with an additional 3 days. Thank you for your time. Kind regards,
Target Market(s)
Thank you so much for your reply and interest.
Our vision is to build a sleek and reliable catalogue to consolidate the products of our vendors and partners in one unique catalogue, we could enrich in the future with additional references and brands.
Our targets are retailers and distributors globally, specialized in Food & Beverages.
We would love to end the catalogue with an order form where customers can place orders.
Industry/Entity Type
Trade
Requirements
Must have
- Thank you so much for your reply and interest.
The catalogue should be easy to modified when we have new brands and items.
Also the draft is in Spanish, but we will translate to English next month.
Horizontal orientation, not Vertical, please.
I have uploaded also a catalogue we like, here attached called "EL BROTANO"
We would love to have a page separation " ideally with a relevant picture or vector" in between each product category: for instance, Wine, then Olive oil, then Cheese, Spanish Ham, etc
We really appreciate your inputs and expertise ;)
We would love to include a map of the products location.
Moreover, a mention to underline the awards or rate won by the product, would be great.
Regarding the range of color. We do trust your knowledge and are open to your creativity.
Feel free to require additional information, we left out.
Many Thanks,
Nice to have
- We do not think our logo would fit nicely on the catalogue inside pages (unless in black) and for that reason would rather have our contact details instead - written in black - as such : Velmoris & Trade - info@Velmoris-Trade.example - Tel : +34 *** *** ***
We prefer "justify" the text. Thanks.
Moreover, we would love to have several pages structures, according to the number of items we have per brands. For instance, some pages with 1 product only, 2 or 3 or 5 up to 6 products per page.

```html
<!DOCTYPE html>
<html lang="en">
<head>
<meta charset="utf-8">
<title>Velmoris &amp; Trade — Food and Beverages Catalogue 2014</title>
<link rel="stylesheet" href="https://fonts.googleapis.com/css2?family=Montserrat:ital,wght@0,800;1,700&family=Raleway:wght@300&family=Oswald:wght@700&display=swap">
<style>
  :root {
    --ink-white: #ffffff;
    --bar-black: #0c0c0c;
    --vine-red: #b8240e;
    --vine-orange: #e2650f;
    --sun-amber: #f4a21c;
    --grape-yellow: #f2d34a;
    --sky-teal: #3f97a6;
    --stone-brown: #6e3a1d;
  }
  * { margin: 0; padding: 0; box-sizing: border-box; }
  html, body { width: 1200px; height: 820px; overflow: hidden; background: #000; }
  .cover {
    position: relative;
    width: 1200px;
    height: 820px;
    overflow: hidden;
    font-family: "Montserrat", sans-serif;
    color: var(--ink-white);
  }
  .cover-photo {
    position: absolute;
    inset: 0;
    background:
      radial-gradient(ellipse 38% 30% at 92% 14%, var(--sky-teal) 0%, rgba(63,151,166,0.6) 45%, rgba(63,151,166,0) 100%),
      radial-gradient(ellipse 30% 26% at 45% 62%, var(--grape-yellow) 0%, rgba(242,211,74,0) 100%),
      radial-gradient(ellipse 28% 22% at 12% 68%, var(--stone-brown) 0%, rgba(110,58,29,0) 100%),
      linear-gradient(160deg, var(--vine-orange) 0%, var(--sun-amber) 35%, var(--vine-orange) 60%, var(--vine-red) 100%);
  }
  .title-mark {
    position: absolute;
    left: 0;
    top: 0;
    width: 1200px;
    height: 300px;
  }
  .title-word {
    position: absolute;
    font-weight: 800;
    line-height: 1;
    letter-spacing: -2px;
    white-space: nowrap;
  }
  .title-food { left: 62px; top: 64px; font-size: 128px; }
  .title-beverages { left: 470px; top: 166px; font-size: 112px; }
  .title-and {
    position: absolute;
    left: 447px;
    top: 170px;
    font-style: italic;
    font-weight: 700;
    font-size: 24px;
    letter-spacing: 1px;
    transform: rotate(-68deg);
    transform-origin: center;
  }
  .brand-bar {
    position: absolute;
    left: 0;
    bottom: 0;
    width: 768px;
    height: 153px;
    background: var(--bar-black);
  }
  .brand-name {
    position: absolute;
    left: 38px;
    top: 60px;
    display: flex;
    align-items: center;
    gap: 14px;
    font-family: "Raleway", sans-serif;
    font-weight: 300;
    font-size: 36px;
    color: var(--ink-white);
    white-space: nowrap;
  }
  .brand-square {
    width: 22px;
    height: 22px;
    background: var(--ink-white);
  }
  .brand-divider {
    position: absolute;
    left: 538px;
    top: 65px;
    width: 3px;
    height: 64px;
    background: var(--ink-white);
  }
  .edition {
    position: absolute;
    left: 581px;
    top: 66px;
    font-family: "Oswald", sans-serif;
    font-weight: 700;
    text-align: center;
    line-height: 1;
  }
  .edition-year { font-size: 38px; display: block; letter-spacing: 1px; }
  .edition-label { font-size: 11px; display: block; letter-spacing: 0.5px; margin-top: 3px; }
</style>
</head>
<body>
  <main class="cover">
    <div class="cover-photo" role="img" aria-label="Sunlit vineyard terrace with a bottle of white wine, a filled wine glass, bunches of grapes and a wedge of cheese on a stone wall"></div>

    <svg class="title-mark" viewBox="0 0 1200 300" aria-hidden="true">
      <line x1="503" y1="68" x2="447" y2="238" stroke="#ffffff" stroke-width="3"/>
      <line x1="513" y1="134" x2="470" y2="262" stroke="#ffffff" stroke-width="3"/>
    </svg>
    <h1>
      <span class="title-word title-food">FOOD</span>
      <span class="title-and">AND</span>
      <span class="title-word title-beverages">BEVERAGES</span>
    </h1>

    <footer class="brand-bar">
      <div class="brand-name"><span>Velmoris &amp; Trade</span><span class="brand-square"></span></div>
      <div class="brand-divider"></div>
      <div class="edition">
        <span class="edition-year">2014</span>
        <span class="edition-label">CATALOGUE</span>
      </div>
    </footer>
  </main>
</body>
</html>
```